Brightfen Business Card Redesign & Logo Update

We need to update our business cards to something more modern and fresh. Brightfen can provide the current color schemes and old design examples, but welcome creativity in helping us with this redesign. PLEASE NOTE that we no longer utilize the "tree" and/or "leaf" imagery in our branding. If able would apprecaite an update on the quality of our "words only" logo in Ai. / PNG formats too.

Target Market(s)

Investors, landowners, corporate partners, contractors

Industry/Entity Type

Environmental Restoration & Conservation

Contact Information for Business Card

Logo, persons name, title, mailing address, phone and email, website url

Font styles to use
Other font styles liked:
• Merriweather

Requirements
Nice to have
• Logo, persons name, title, mailing address, phone and email, website url, but open to ideams
Should not have
• No all back backgrounds

```html
<!DOCTYPE html>
<html lang="en">
<head>
<meta charset="UTF-8">
<title>Brightfen Business Card</title>
<link rel="stylesheet" href="https://fonts.googleapis.com/css2?family=Merriweather:wght@400;700;900&display=swap">
<style>
  :root {
    --bg: #e6e7e8;
    --card: #ffffff;
    --green: #1a7a3c;
    --orange: #e8781f;
    --ink: #1d1d1b;
    --white: #ffffff;
  }
  * { box-sizing: border-box; margin: 0; padding: 0; }
  html, body {
    width: 1200px; height: 1059px; overflow: hidden;
    background: var(--bg);
    font-family: "Merriweather", Georgia, serif;
    color: var(--ink);
  }
  .sheet {
    position: relative; width: 1200px; height: 1059px;
    display: flex; flex-direction: column; align-items: center; justify-content: center;
    gap: 60px;
  }
  .card {
    position: relative; width: 700px; height: 400px;
    background: var(--card);
    box-shadow: 0 8px 24px rgba(0,0,0,0.18);
    overflow: hidden;
  }
  .brand {
    display: flex; flex-direction: column; align-items: center;
  }
  .brand-name {
    font-weight: 900; font-size: 64px; letter-spacing: 2px;
    color: var(--green); text-transform: uppercase; line-height: 1;
  }
  .brand-tagline {
    margin-top: 8px;
    font-weight: 700; font-size: 15px; letter-spacing: 2.2px;
    text-transform: uppercase; color: var(--ink);
  }
  .card-front { display: flex; align-items: center; justify-content: center; }
  .card-back .brand { position: absolute; top: 62px; left: 0; right: 0; }
  .card-back .brand-name { font-size: 54px; }
  .card-back .brand-tagline { font-size: 13px; margin-top: 7px; }

  .details {
    position: absolute; top: 190px; left: 0; right: 0;
    display: flex; justify-content: center; align-items: stretch;
  }
  .person {
    text-align: right; padding-right: 16px;
    display: flex; flex-direction: column; justify-content: flex-end;
    padding-top: 40px;
  }
  .person-name { font-weight: 900; font-size: 21px; text-transform: uppercase; }
  .person-name .first { color: var(--orange); }
  .person-name .last { color: var(--green); }
  .person-title { font-size: 16px; margin-top: 2px; }
  .divider { width: 2px; background: var(--green); }
  .contacts {
    list-style: none; padding-left: 14px;
    display: flex; flex-direction: column; gap: 3px;
    font-size: 16px;
  }
  .contacts li { display: flex; align-items: center; gap: 7px; }
  .contacts svg { width: 13px; height: 13px; fill: var(--green); flex: none; }
  .address-band {
    position: absolute; left: 0; right: 0; bottom: 18px; height: 58px;
    background: var(--green); color: var(--white);
    display: flex; align-items: center; justify-content: center;
    font-size: 18px; letter-spacing: 0.3px;
  }
</style>
</head>
<body>
<main class="sheet">
  <section class="card card-front">
    <div class="brand">
      <span class="brand-name">Brightfen</span>
      <span class="brand-tagline">Environmental Credit Company</span>
    </div>
  </section>

  <section class="card card-back">
    <div class="brand">
      <span class="brand-name">Brightfen</span>
      <span class="brand-tagline">Environmental Credit Company</span>
    </div>
    <div class="details">
      <div class="person">
        <div class="person-name"><span class="first">Miles</span> <span class="last">Carver</span></div>
        <div class="person-title">Founder</div>
      </div>
      <div class="divider"></div>
      <ul class="contacts">
        <li>
          <svg viewBox="0 0 16 16" aria-hidden="true"><path d="M3.6 1.2l2.4 2.6-1.3 1.9c.9 2 2.5 3.6 4.6 4.6l1.9-1.3 2.6 2.4-1.4 2.4C6.8 13.6 2.4 9.2 1.2 3.6z"/></svg>
          (555) 214-3390
        </li>
        <li>
          <svg viewBox="0 0 16 16" aria-hidden="true"><path d="M1 3h14v10H1z M1.5 3.5L8 8.8l6.5-5.3" stroke="#fff" stroke-width="1.2"/></svg>
          hello@brightfenmail.com
        </li>
        <li>
          <svg viewBox="0 0 16 16" aria-hidden="true"><circle cx="8" cy="8" r="7"/><path d="M1 8h14M8 1c-3 3.5-3 10.5 0 14M8 1c3 3.5 3 10.5 0 14" stroke="#fff" stroke-width="1" fill="none"/></svg>
          www.brightfenco.com
        </li>
      </ul>
    </div>
    <div class="address-band">48 Marsh Lane, Suite 12, PO 7218, Fenwick</div>
  </section>
</main>
</body>
</html>
```